Kestrel Motion LLC Sports Therapy and Soft Tissue Injury solutions

We are a company that specializes in Sports Therapy, Physical therapy, muscular rehab, nutrition plans, and personal training. Kestrel Motion travels around the country and world treating athletes and people in the workforce that have Soft Tissue injuries. We are legally partnered with VMR(Vantor Muscle Recovery/vantorrecovery.example) in treating endurance athletes ex. SteelRidge triathalon. We educate our patients on how to sustain a healthy lifestyle.We need a web design that has a Home page summarizing our services, a Physical therapy page, a Personal training and nutrition page. Our ultimate goal is to build relationships with fitness centers, training facilities, and companies that are implementing preventative health measures for their employees. We want to incorporate the VMR logo and Steelridge logo attached in the website but, we want to use our own name (Kestrel Motion LLC) as the main draw. We will provide literature for the website.

Target Market(s)

Grindlane training gyms, Fitness centers, Dance studios, Companies looking for Corporate Wellness programs

Industry/Entity Type

Health And Wellness

Number of Pages Required

4 page

Font styles to use
Sans Serif

Requirements
Must have
• Stock Photos of Athletes training. Examples of Endurance Athletes and Cross training. A mesh of as many sports and training methods as possible. We are a new company and don't have many photos. Easy accessibility to change and add text as the company grows. Vantor Muscle recovery logo incorporated in the back ground of the website. Always visible but does not take over the web page
Nice to have
• Sleek and cool, and masculine design. We want the website to stand out without focusing on one individual. We want to use the website to brand the company (Kestrel Motion LLC) with easy access to social media platforms

```html
<!DOCTYPE html>
<html lang="en">
<head>
<meta charset="utf-8">
<title>Kestrel Motion LLC — Contact Us</title>
<link href="https://fonts.googleapis.com/css2?family=Anton&family=Open+Sans:ital,wght@0,400;0,600;0,700;1,400&family=Roboto:wght@700&display=swap" rel="stylesheet">
<style>
:root{
  --red:#d0021b;
  --ink:#222;
  --text:#555;
  --light:#f5f5f5;
  --black:#111;
  --footer:#1b1b1b;
  --white:#fff;
  --line:#d8d8d8;
}
*{box-sizing:border-box;margin:0;padding:0}
html,body{width:1200px;height:2995px;overflow:hidden}
body{font-family:"Open Sans",sans-serif;color:var(--text);background:var(--white);position:relative}
.heading{font-family:"Anton",sans-serif;font-weight:400;text-transform:uppercase;color:var(--ink);letter-spacing:.5px}
.heading .accent{color:var(--red)}

/* nav */
.topbar{position:absolute;left:0;top:0;width:1200px;height:66px;background:var(--black)}
.brand{position:absolute;left:160px;top:18px;font-family:"Roboto",sans-serif;font-weight:700;font-size:19px;color:var(--white)}
.nav{position:absolute;right:160px;top:0;display:flex;height:66px}
.nav a{font-family:"Anton",sans-serif;font-size:11px;color:var(--white);text-decoration:none;text-transform:uppercase;line-height:66px;margin-left:48px;position:relative;letter-spacing:.4px}
.nav a.active::after{content:"";position:absolute;left:50%;bottom:0;width:28px;height:3px;margin-left:-14px;background:var(--red)}

/* hero */
.hero{position:absolute;left:0;top:66px;width:1200px;height:454px;background:radial-gradient(ellipse at 40% 35%,#8a8a8a 0%,#4a4a4a 40%,#1e1e1e 100%)}
.hero-title{position:absolute;left:0;width:1200px;top:164px;text-align:center;font-family:"Anton",sans-serif;font-size:36px;color:var(--white);letter-spacing:.5px}
.hero-sub{position:absolute;left:340px;width:520px;top:222px;text-align:center;font-size:15px;font-weight:600;line-height:25px;color:var(--white)}

/* programs */
.programs{position:absolute;left:0;top:520px;width:1200px;height:1320px;background:var(--light)}
.section-title{position:absolute;left:0;width:1200px;text-align:center;font-size:24px}
.section-intro{position:absolute;text-align:center;font-size:10.5px;line-height:20px;color:var(--text)}
.card{position:absolute;width:426px;background:var(--white);box-shadow:0 2px 8px rgba(0,0,0,.12)}
.card-photo{display:block;width:426px;height:232px}
.card-title{margin:38px 24px 0;font-size:16px}
.card-text{margin:14px 24px 0;font-size:10.5px;line-height:20px;color:var(--text)}
.card-price{position:absolute;left:24px;bottom:22px;font-family:"Open Sans",sans-serif;font-weight:700;font-size:20px;color:var(--red)}
.card-more{position:absolute;right:0;bottom:0;width:46px;height:42px;background:var(--red);display:flex;align-items:center;justify-content:center}

/* contact */
.contact-form{position:absolute;left:360px;top:2046px;width:482px}
.field{display:block;width:482px;height:36px;border:1px solid var(--line);margin-bottom:3px;font-style:italic;font-size:10.5px;color:#444;padding:9px 8px}
.field.message{height:80px}
.submit{display:block;margin-top:7px;width:92px;height:38px;background:var(--red);color:var(--white);font-family:"Anton",sans-serif;font-size:12px;text-align:center;line-height:38px;letter-spacing:.4px}

.map{position:absolute;left:0;top:2342px;width:1200px;height:310px;background:linear-gradient(160deg,#6e6e6e,#8a8a8a 50%,#6a6a6a)}

/* footer */
.footer{position:absolute;left:0;top:2652px;width:1200px;height:343px;background:var(--footer)}
.signup-title{position:absolute;left:162px;top:34px;font-family:"Anton",sans-serif;font-size:20px;color:var(--white);letter-spacing:.5px}
.signup-input{position:absolute;left:622px;top:28px;width:330px;height:38px;background:#2e2e2e;color:#aaa;font-size:10px;padding:12px 12px}
.signup-btn{position:absolute;left:952px;top:28px;width:88px;height:38px;background:var(--red);color:var(--white);font-family:"Anton",sans-serif;font-size:11px;text-align:center;line-height:38px}
.footer-rule{position:absolute;left:162px;top:100px;width:878px;height:1px;background:#333}
.footer-col{position:absolute;top:142px}
.footer-col h4{font-family:"Anton",sans-serif;font-weight:400;font-size:10px;color:var(--white);margin-bottom:14px;letter-spacing:.3px}
.footer-col li{list-style:none;font-size:10.5px;color:#9a9a9a;line-height:22px}
.copyright{position:absolute;left:162px;top:308px;font-size:10px;color:#9a9a9a}
.social{position:absolute;left:856px;top:304px;display:flex;gap:14px}
.social span{width:14px;height:14px;border-radius:50%;background:var(--white)}
</style>
</head>
<body>

<header class="topbar">
  <div class="brand">Kestrel Motion LLC</div>
  <nav class="nav">
    <a href="#">Home</a>
    <a href="#">Services</a>
    <a href="#">Physical Therapy</a>
    <a href="#">Personal Training</a>
    <a href="#">Nutrition</a>
    <a href="#" class="active">Contact Us</a>
  </nav>
</header>

<section class="hero" role="img" aria-label="Black and white photo of a trainer spotting an athlete lifting dumbbells">
  <h1 class="hero-title">CONTACT US</h1>
  <p class="hero-sub">Sed ut perspiciatis unde omnloreis isteit voluaccusantium doloremue lauloredantiumtota mrem aperiameaue sa lauloredub illo.</p>
</section>

<section class="programs">
  <h2 class="heading section-title" style="top:68px">Programs and <span class="accent">Pricing</span></h2>
  <p class="section-intro" style="left:262px;width:676px;top:114px">Sed ut perspiciatis unde omnis iste natus sitolu ptatem accusantium doloremque laudantium, totme maperiam, eaque ipsa quae ab illo inventore veritati quasi archite ed ut perspiciatis unde omnis iste natus sitolu ptatem accusantium doloremque laudantium, totme maperiamaque ipsa quae ab illo inventore veritati quasiar hit ecterspiciatis unde omnis iste natus sitolu.</p>

  <article class="card" style="left:162px;top:206px;height:484px">
    <div class="card-photo" role="img" aria-label="Photo of two athletes lifting barbells in a brick-walled gym" style="background:linear-gradient(135deg,#c9b8a6,#8a6f5c 55%,#4d4a4a)"></div>
    <h3 class="heading card-title">Marcus Hale-Owner/Operator</h3>
    <p class="card-text">Sed ut perspiciatis unde omnis iste natus sitolu ptatem accusantium dolor emque laudantium, totme maperiam, eaque ipsa quae ab illo inventore ve ritati quasi archite ed ut perspiciatis unde omnis iste natus sitolu ptatem accusantium doloremque laudantium, totme maperiamaque ipsa quae ab illo inventore veritati quasiar hit ecterspiciatis unde omnis iste.</p>
    <div class="card-price">$ 258.00</div>
    <div class="card-more"><svg width="10" height="8" viewBox="0 0 10 8"><path d="M1 1l3 3-3 3M5 1l3 3-3 3" fill="none" stroke="#fff" stroke-width="1.6"/></svg></div>
  </article>

  <article class="card" style="left:612px;top:206px;height:484px">
    <div class="card-photo" role="img" aria-label="Photo of a woman doing push-ups with a trainer in a bright gym" style="background:linear-gradient(135deg,#e8e4de,#a99b8c 55%,#5a4e46)"></div>
    <h3 class="heading card-title">VMR Full Body Certified Practitione</h3>
    <p class="card-text">Sed ut perspiciatis unde omnis iste natus sitolu ptatem accusantium dolor emque laudantium, totme maperiam, eaque ipsa quae ab illo inventore ve ritati quasi archite ed ut perspiciatis unde omnis iste natus sitolu ptatem accusantium doloremque laudantium, totme maperiamaque ipsa quae ab illo inventore veritati quasiar hit ecterspiciatis unde omnis iste.</p>
    <div class="card-price">$ 258.00</div>
    <div class="card-more"><svg width="10" height="8" viewBox="0 0 10 8"><path d="M1 1l3 3-3 3M5 1l3 3-3 3" fill="none" stroke="#fff" stroke-width="1.6"/></svg></div>
  </article>

  <article class="card" style="left:162px;top:732px;height:486px">
    <div class="card-photo" role="img" aria-label="Photo of a green apple, fresh salad and a measuring tape on a wooden table" style="background:linear-gradient(135deg,#6b8a3a,#4a5e2c 45%,#5a4a44)"></div>
    <h3 class="heading card-title">Fitness and Nutrition Consultant</h3>
    <p class="card-text">Sed ut perspiciatis unde omnis iste natus sitolu ptatem accusantium dolor emque laudantium, totme maperiam, eaque ipsa quae ab illo inventore ve ritati quasi archite ed ut perspiciatis unde omnis iste natus sitolu ptatem accusantium doloremque laudantium, totme maperiamaque ipsa quae ab illo inventore veritati quasiar hit ecterspiciatis unde omnis iste.</p>
    <div class="card-price">$ 258.00</div>
    <div class="card-more"><svg width="10" height="8" viewBox="0 0 10 8"><path d="M1 1l3 3-3 3M5 1l3 3-3 3" fill="none" stroke="#fff" stroke-width="1.6"/></svg></div>
  </article>

  <article class="card" style="left:612px;top:732px;height:486px">
    <div class="card-photo" role="img" aria-label="Photo of a trainer guiding a woman through a sit-up exercise" style="background:linear-gradient(135deg,#d6d3d0,#8f8a88 55%,#3c3a3e)"></div>
    <h3 class="heading card-title">Licensed Massage Therapist</h3>
    <p class="card-text">Sed ut perspiciatis unde omnis iste natus sitolu ptatem accusantium dolor emque laudantium, totme maperiam, eaque ipsa quae ab illo inventore ve ritati quasi archite ed ut perspiciatis unde omnis iste natus sitolu ptatem accusantium doloremque laudantium, totme maperiamaque ipsa quae ab illo inventore veritati quasiar hit ecterspiciatis unde omnis iste.</p>
    <div class="card-price">$ 258.00</div>
    <div class="card-more"><svg width="10" height="8" viewBox="0 0 10 8"><path d="M1 1l3 3-3 3M5 1l3 3-3 3" fill="none" stroke="#fff" stroke-width="1.6"/></svg></div>
  </article>
</section>

<section class="contact">
  <h2 class="heading section-title" style="top:1896px">Get in <span class="accent">Touch!!</span></h2>
  <p class="section-intro" style="left:348px;width:504px;top:1950px">Sed ut perspiciatis unde omnis iste natus sitolu ptatem accusantium doloremque laudantium, totme maperiam, eaque ipsa quae ab illo inventore veritati quasi archite ed ut perspiciatis unde omnis iste natus sitolu ptatem accusantium doloritati quasi archite ed &nbsp;emque laudantium.</p>
  <form class="contact-form">
    <div class="field">Name:</div>
    <div class="field">Phone:</div>
    <div class="field">Email:</div>
    <div class="field message">Message:</div>
    <div class="submit">SUBMIT</div>
  </form>
</section>

<div class="map" role="img" aria-label="Grayscale street map showing the studio location downtown"></div>

<footer class="footer">
  <div class="signup-title">SIGN UP FOR THE LATEST NEWS AND OFFERS</div>
  <div class="signup-input">Enter Email Address:</div>
  <div class="signup-btn">SIGN UP</div>
  <div class="footer-rule"></div>

  <div class="footer-col" style="left:162px"><h4>FOR CONSUMERS</h4><ul><li>Disclosures</li><li>Investor Relations</li><li>Corporate Governance</li><li>Newsroom</li></ul></div>
  <div class="footer-col" style="left:366px"><h4>BUSINESS</h4><ul><li>Partners</li><li>Blog</li><li>Company</li><li>Resources</li></ul></div>
  <div class="footer-col" style="left:530px"><h4>COMPANY</h4><ul><li>Nutrition</li><li>Dietary Science</li><li>Recipe/Food Prep</li><li>Training</li></ul></div>
  <div class="footer-col" style="left:710px"><h4>HELP</h4><ul><li>Terms</li><li>Privacy</li><li>Contact us</li></ul></div>
  <div class="footer-col" style="left:860px"><h4>CONTACT US FOR PROGRAMS</h4><ul><li>2280 W. Larkspur Ave Suite 410</li><li>Fairview, California, 90000</li><li>Phone: (555) 014-2290</li></ul></div>

  <div class="copyright">© 2017 Kestrel Motion LLC. All Copyrights are Reserved. Terms of Use.Certification # 00000</div>
  <div class="social" aria-label="Social media links"><span></span><span></span><span></span><span></span><span></span><span></span></div>
</footer>

</body>
</html>
```